Flyer Design for Dental Harborline

Hi everyone,
Just looking to create a double-sided full colour DL-sized (210mm x 99mm) flyer for a new dental practice called Dental Harborline. The flyers will be distributed in letterboxes (along with a fridge magnet stuck onto it) around the nearby suburbs (approx. 10 000 flyers will be printed and delivered).
We have already got a logo and a preliminary website design as attached, and we would like the design of the brochure to match this. We would like the attached information presented in a neat, tidy and eye-catching manner for the flyer, along with stock imagery where required. The flyer will be orientated vertically.
Details of the location and opening hours can be found at www.dentalharborline.com.au. Please ignore the logo used on this site as it is only temporary.
Industry/Entity Type
Dental
Requirements
Must have
- Brochure Content
(Please note that the intention of the bold items is to have them highlighted at the top of the flyer). Please use stock imagery as required and we can buy them once final.
Front of the flyer: (in any order you think best)
- (In Bold writing) SPECIAL OFFER: Free check-ups for all new patients – valued at $6o!*
- “New dentist now open!”
- Emergency appointments available – call now!
- Bring the kids to feed the fish in our marine tank!
- Intraoral cameras
- Dental Harborline Logo
- Call us now: 3715 4062 or book online at www.dentalharborline.com.au
Also, we would like the following terms and conditions for the special offers in small font:
“Item code 011 only. Valid for appointments attended before 30th April 2013. Not to be used in conjunction with any other offer.”
Back of the flyer: (in any order you think best)
- (In Bold writing) Line 1: Scared of Needles?
- (In Bold writing) Line 2 (maybe with picture in between?): Try our needle free injection today!*
- Dental Harborline Logo
- Our Location – address and picture
- Our phone number: 3715 4062 (please make this prominent)
- A QR code (we can supply this to you shortly)
- Opening hours
- Our website: www.dentalharborline.com.au
*suitable candidates only
The colours primarily used are blues and greys, so please don’t stray too far away from this colour scheme.

```html
<!DOCTYPE html>
<html lang="en">
<head>
<meta charset="utf-8">
<title>Dental Harborline – DL Flyer</title>
<link rel="stylesheet" href="https://fonts.googleapis.com/css2?family=Roboto:wght@300;400;500;700;900&family=Oswald:wght@400;500&display=swap">
<style>
  :root {
    --stage: #707070;
    --paper: #efefef;
    --navy: #1e2a4f;
    --teal: #62bfc5;
    --ink: #3f3f3f;
    --white: #ffffff;
    --body: "Roboto", Arial, sans-serif;
    --condensed: "Oswald", "Arial Narrow", sans-serif;
  }
  * { margin: 0; padding: 0; box-sizing: border-box; }
  html, body { width: 1200px; height: 1168px; overflow: hidden; }
  body { background: var(--stage); font-family: var(--body); position: relative; }

  .flyer { position: absolute; top: 92px; width: 455px; height: 965px; background: var(--paper); overflow: hidden; box-shadow: 0 1px 3px rgba(0,0,0,.25); }
  .flyer--front { left: 98px; }
  .flyer--back { left: 628px; }
  .abs { position: absolute; }

  .photo { position: absolute; }
  .photo--checkup { left: 0; top: 0; width: 225px; height: 195px; background: linear-gradient(135deg, #e9e3de, #c7d5de 60%, #6fb9c9); }
  .photo--chair { left: 232px; top: 0; width: 223px; height: 225px; background: linear-gradient(160deg, #eef0f2, #b9c9de 55%, #d9d2cc); }
  .photo--team { left: 0; top: 231px; width: 455px; height: 207px; background: linear-gradient(110deg, #c9d4df, #e6ecf0 45%, #d8e2e8 70%, #a9c7d8); }
  .photo--needle { left: 0; top: 0; width: 455px; height: 318px; background: linear-gradient(120deg, #e4e4e4, #d7d0c9 50%, #b59b88 80%, #5e4a3e); }

  .tag-new { left: 0; top: 195px; width: 322px; height: 34px; background: var(--navy); color: var(--white); font-size: 19px; font-weight: 400; line-height: 34px; padding-left: 33px; }

  .offer-head { left: 0; top: 438px; width: 455px; height: 69px; background: var(--navy); color: var(--white); font-weight: 900; font-size: 48px; line-height: 69px; padding-left: 23px; letter-spacing: .5px; }
  .offer-band { left: 0; top: 507px; width: 455px; height: 99px; background: var(--teal); color: var(--white); }
  .offer-band__text { position: absolute; left: 22px; top: 20px; font-family: var(--condensed); font-size: 23px; line-height: 32px; font-weight: 400; }
  .offer-band__price { position: absolute; left: 254px; top: -6px; font-family: var(--condensed); font-size: 96px; line-height: 110px; font-weight: 500; letter-spacing: -2px; }
  .offer-bang { left: 406px; top: 455px; width: 50px; height: 150px; }
  .offer-terms { left: 0; top: 606px; width: 455px; height: 55px; background: var(--navy); color: var(--white); font-size: 12px; line-height: 16px; text-align: center; padding-top: 12px; }
  .offer-terms strong { font-weight: 700; }

  .features { left: 30px; top: 680px; list-style: none; color: var(--ink); font-size: 16px; font-weight: 300; }
  .features li { height: 29px; line-height: 22px; padding-left: 29px; position: relative; }
  .features li::before { content: ""; position: absolute; left: 0; top: 10px; width: 5px; height: 5px; border-radius: 50%; background: var(--ink); }

  .brand { display: flex; align-items: center; gap: 12px; }
  .brand__mark { width: 34px; height: 34px; background: var(--navy); }
  .brand__name { font-size: 27px; font-weight: 500; color: var(--navy); letter-spacing: .2px; }
  .brand--front { left: 28px; top: 793px; }
  .brand--back { left: 42px; top: 738px; }

  .contact { color: var(--ink); }
  .contact__label { font-size: 13px; font-weight: 300; line-height: 16px; }
  .contact__phone { font-size: 27px; font-weight: 400; color: var(--navy); line-height: 32px; margin-bottom: 4px; }
  .contact__web { font-size: 27px; font-weight: 400; color: var(--navy); line-height: 30px; }
  .contact--front { left: 27px; top: 852px; }
  .contact--back { left: 41px; top: 842px; }

  .needles-tag { left: 0; top: 325px; width: 372px; height: 56px; }
  .needles-tag__text { position: absolute; left: 39px; top: 326px; color: var(--white); font-size: 33px; font-weight: 300; line-height: 52px; }
  .needles-head { left: 39px; top: 397px; color: var(--navy); font-size: 33px; font-weight: 400; line-height: 39px; }
  .needles-note { left: 43px; top: 481px; font-size: 13px; color: #222; }

  .hours { left: 40px; top: 515px; width: 376px; border-collapse: collapse; font-size: 13px; font-weight: 300; color: var(--ink); }
  .hours th { background: var(--navy); color: var(--white); font-weight: 700; text-align: left; height: 34px; padding-left: 15px; letter-spacing: .4px; }
  .hours td { height: 26.3px; }
  .hours td:first-child { padding-left: 15px; width: 105px; }
  .hours tr.is-alt td { background: var(--navy); color: var(--white); font-weight: 400; }
  .hours tr + tr td { border-top: 1px solid var(--paper); }

  .address { left: 42px; top: 792px; font-size: 14px; line-height: 17px; color: var(--ink); font-weight: 300; }
</style>
</head>
<body>

<section class="flyer flyer--front" aria-label="Flyer front">
  <div class="photo photo--checkup" role="img" aria-label="Stock photo: patient smiling during a dental check-up"></div>
  <div class="photo photo--chair" role="img" aria-label="Stock photo: patient relaxing in a dental chair"></div>
  <div class="abs tag-new">“NEW DENTIST NOW OPEN!”</div>
  <div class="photo photo--team" role="img" aria-label="Stock photo: dentist and assistant treating a patient in the surgery"></div>

  <div class="abs offer-head">SPECIAL OFFER</div>
  <div class="abs offer-band">
    <div class="offer-band__text">FREE CHECK-UPS FOR ALL<br>NEW PATIENTS VALUED AT</div>
    <div class="offer-band__price">$60</div>
  </div>
  <svg class="abs offer-bang" viewBox="0 0 50 150" aria-hidden="true">
    <polygon points="16,0 36,0 26,102 12,102" fill="#ffffff"/>
    <polygon points="9,116 24,116 22,134 7,134" fill="#ffffff"/>
  </svg>
  <div class="abs offer-terms">“Item code 011 only. Valid for appointments attended before<br><strong>30th April 2013</strong>. Not to be used in conjunction with any other offer.”</div>

  <ul class="abs features">
    <li>Emergency appointments available – call now!</li>
    <li>Bring the kids to feed the fish in our marine tank!</li>
    <li>Intraoral cameras</li>
  </ul>

  <div class="abs brand brand--front">
    <span class="brand__mark"></span>
    <span class="brand__name">Dental Harborline</span>
  </div>

  <div class="abs contact contact--front">
    <p class="contact__label">Call us now:</p>
    <p class="contact__phone">3715 4062</p>
    <p class="contact__label">or book online at</p>
    <p class="contact__web">www.dentalharborline.com.au</p>
  </div>
</section>

<section class="flyer flyer--back" aria-label="Flyer back">
  <div class="photo photo--needle" role="img" aria-label="Stock photo: anxious patient facing a dental syringe"></div>
  <svg class="abs needles-tag" viewBox="0 0 372 56" aria-hidden="true">
    <polygon points="0,0 372,0 320,56 0,56" fill="#1e2a4f"/>
  </svg>
  <div class="abs needles-tag__text">Scared of Needles?</div>

  <h2 class="abs needles-head">TRY OUR NEEDLE FREE<br>INJECTION TODAY!*</h2>
  <p class="abs needles-note">*suitable candidates only</p>

  <table class="abs hours">
    <tr><th colspan="2">OPENING HOURS</th></tr>
    <tr><td>Monday</td><td>8:00 am – 8:00 pm</td></tr>
    <tr class="is-alt"><td>Tuesday</td><td>8:00 am – 8:00 pm</td></tr>
    <tr><td>Wednesday</td><td>8:00 am – 8:00 pm</td></tr>
    <tr class="is-alt"><td>Thursday</td><td>8:00 am – 8:00 pm</td></tr>
    <tr><td>Friday</td><td>8:00 am – 5:30 pm</td></tr>
    <tr class="is-alt"><td>Saturday</td><td>9:00 am – 2:00 pm</td></tr>
  </table>

  <div class="abs brand brand--back">
    <span class="brand__mark"></span>
    <span class="brand__name">Dental Harborline</span>
  </div>

  <p class="abs address">2217-2231 Coral Bay Hwy, Marina Square Shopping Centre,<br>Eastbrook, Queensland, 4120</p>

  <div class="abs contact contact--back">
    <p class="contact__label">Call us now:</p>
    <p class="contact__phone">3715 4062</p>
    <p class="contact__label">or book online at</p>
    <p class="contact__web">www.dentalharborline.com.au</p>
  </div>
</section>

</body>
</html>
```